Website for enterprise software start-up

We need a new Wordpress website. We are an early stage start-up focused on mobile video technology for cellular operators. The audience is strategy, marketing and customer acquisition execs from the operators.

The purpose of the site is to act as a sales brochure and capture leads. A demo app can be downloaded from the current site, want to put that behind a contact form.

Current website is at www.velmora.tv. Similar number of pages. Looking for a clean design template, with minimal customization. Blog will remain as is.

Want to be able to modify the copy via Wordpress. Reference designs I like: quandrix.com, briskfold7metrics.com

Target Market(s)

Mobile operators and MVNOs in the US and Asia Pacific regions

Industry/Entity Type

Business Software

Coding

Coded - Design and coding required

Number of Pages Required

4 page

Font styles to use
Sans Serif

Colors
f78f20

Requirements
Must have
• Form for downloading sample apps.
• Landing page with image, Product, Blog, About, Contact
• Team page

```html
<!DOCTYPE html>
<html lang="en">
<head>
<meta charset="utf-8">
<title>Velmora Media</title>
<link href="https://fonts.googleapis.com/css2?family=Roboto:wght@300;400;500;700&display=swap" rel="stylesheet">
<style>
:root{
  --orange:#f78f20;
  --orange-deep:#e8760f;
  --ink:#333333;
  --muted:#6f6f6f;
  --dark:#1e1e1e;
  --paper:#ffffff;
  --line:#d9d9d9;
}
*{box-sizing:border-box;margin:0;padding:0}
html,body{width:1200px;height:2862px;overflow:hidden}
body{font-family:"Roboto",Arial,sans-serif;color:var(--ink);background:var(--paper);position:relative}
section,header,footer{position:absolute;left:0;width:1200px}
.brand{display:flex;align-items:center;gap:10px}
.brand-mark{width:54px;height:54px;background:var(--orange)}
.brand-name{font-weight:700;font-size:50px;letter-spacing:-1px;color:var(--ink);line-height:1}

/* header */
.site-header{top:0;height:96px;display:flex;align-items:center;justify-content:space-between;padding:0 125px 0 142px}
.main-nav{display:flex;align-items:center}
.main-nav a{font-size:16px;color:var(--ink);text-decoration:none;margin-left:44px}
.main-nav .login{background:var(--orange);color:#fff;padding:8px 20px;margin-left:34px}

/* hero */
.hero{top:96px;height:464px;overflow:hidden}
.hero-photo{position:absolute;inset:0;background:linear-gradient(90deg,#2a211d 0%,#7d6a60 30%,#c9c3c4 60%,#9c9aa2 100%)}
.hero-copy{position:absolute;left:0;right:0;top:150px;text-align:center;color:#fff}
.hero-copy h1{font-size:38px;font-weight:500;margin-bottom:6px}
.hero-copy p{font-size:22px;font-weight:300;line-height:1.3}
.btn-orange{display:inline-block;background:var(--orange);color:#fff;font-size:14px;font-weight:500;text-transform:uppercase;padding:12px 26px;text-decoration:none}
.hero-copy .btn-orange{margin-top:22px}
.hero-arrow{position:absolute;top:200px}
.hero-arrow.prev{left:128px}
.hero-arrow.next{right:130px}

/* partners */
.partners{top:560px;height:95px;background:linear-gradient(#fafafa,#e6e6e6);display:flex;align-items:center;justify-content:space-around;padding:0 130px;border-bottom:1px solid var(--line)}
.partner{width:110px;height:36px;background:#bdbdbd;border-radius:4px}
.partner.round{width:56px;height:56px;border-radius:50%}

/* why */
.why{top:655px;height:366px}
.why-copy{position:absolute;left:157px;top:62px;width:500px}
.section-title{font-size:32px;font-weight:300;color:var(--ink);margin-bottom:22px}
.ticks{list-style:none}
.ticks li{position:relative;padding-left:16px;font-size:13.5px;line-height:1.45;color:var(--muted);margin-bottom:14px}
.ticks li::before{content:"›";position:absolute;left:0;top:-1px;font-size:16px}
.btn-grey{display:inline-block;background:linear-gradient(#a0a0a0,#7b7b7b);color:#fff;font-size:11px;font-weight:500;text-transform:uppercase;padding:11px 24px;margin-top:8px;text-decoration:none}
.why-photo{position:absolute;left:731px;top:18px;width:282px;height:325px;clip-path:polygon(50% 0,100% 25%,100% 75%,50% 100%,0 75%,0 25%);background:linear-gradient(160deg,#8fbf4f,#dfe8c8 60%,#f2ead8)}

/* benefits */
.benefits{top:1021px;height:340px;background:linear-gradient(135deg,var(--orange) 0%,#f9a040 50%,var(--orange-deep) 100%);display:flex;justify-content:center;gap:52px;padding-top:70px}
.benefit{width:280px;text-align:center;color:#fff;font-size:16px;line-height:1.55}
.benefit svg{display:block;margin:0 auto 26px}

/* features */
.features{top:1361px;height:421px;background:var(--dark)}
.features-photo{position:absolute;left:0;top:0;width:588px;height:421px;background:linear-gradient(120deg,#5a4f45,#9a8a78 45%,#3e3a36)}
.features-copy{position:absolute;left:641px;top:54px;width:480px;color:#d8d8d8}
.features-copy .section-title{color:#fff;margin-bottom:20px}
.features-copy .ticks li{color:#cfcfcf;font-size:13px;margin-bottom:18px}
.btn-outline{display:inline-block;border:1px solid #fff;color:#fff;font-size:12px;font-weight:500;text-transform:uppercase;padding:10px 22px;text-decoration:none}

/* push */
.push{top:1782px;height:454px}
.push-copy{position:absolute;left:134px;top:80px;width:480px}
.push-copy .ticks li{font-size:13px}
.push-copy .btn-orange{font-size:11px;padding:11px 24px;margin-top:4px}
.push-phones{position:absolute;left:658px;top:65px;width:372px;height:389px;background:linear-gradient(90deg,#e9eef0 0%,#cfd6da 40%,#2b9be0 42%,#2f2f2f 46%,#3b3430 100%);border-radius:24px 24px 0 0}

/* orbis band */
.orbis{top:2236px;height:302px;overflow:hidden}
.orbis-photo{position:absolute;inset:0;background:linear-gradient(90deg,#cfcfcf,#e2e2e2 40%,#d6d6d6)}
.orbis-copy{position:absolute;left:0;right:0;top:72px;text-align:center}
.orbis-copy h2{font-size:27px;font-weight:400;line-height:1.3;color:var(--ink)}
.orbis-copy p{font-size:18px;font-weight:300;color:#555;margin-top:6px}
.store-badges{display:flex;justify-content:center;gap:8px;margin-top:26px}
.store-badge{width:114px;height:38px;background:#111;border:1px solid #888;border-radius:5px}

/* footer */
.site-footer{top:2538px;height:324px;background:var(--orange);color:#fff}
.foot-col{position:absolute;top:55px}
.foot-col h3{font-size:17px;font-weight:400;margin-bottom:14px}
.foot-col a{display:block;font-size:14px;color:#fff;opacity:.85;text-decoration:none;margin-bottom:12px}
.col-links{left:143px}
.col-services{left:313px}
.col-resources{left:490px}
.col-contact{left:620px}
.col-follow{left:891px}
.field{display:block;width:225px;height:28px;border:1px solid #fff;color:#fff;font-size:11px;padding:0 10px;line-height:26px;margin-bottom:6px}
.btn-submit{display:inline-block;background:#5a2e08;color:#fff;font-size:12px;font-weight:500;padding:7px 22px;margin-top:8px}
.socials{display:flex;gap:12px}
.social{width:34px;height:34px;border:1px solid #fff;border-radius:50%}
.foot-rule{position:absolute;left:143px;right:139px;top:242px;height:1px;background:rgba(255,255,255,.45)}
.copyright{position:absolute;left:143px;top:274px;font-size:12px;opacity:.85}
.site-footer .brand{position:absolute;left:834px;top:258px}
.site-footer .brand-mark{background:#fff;width:44px;height:44px}
.site-footer .brand-name{color:#fff;font-size:42px}
</style>
</head>
<body>

<header class="site-header">
  <div class="brand"><span class="brand-mark"></span><span class="brand-name">velmora</span></div>
  <nav class="main-nav">
    <a href="#">Home</a><a href="#">Products</a><a href="#">Blogs</a><a href="#">About</a><a href="#">Contact</a><a href="#" class="login">Login</a>
  </nav>
</header>

<section class="hero">
  <div class="hero-photo" role="img" aria-label="Person holding a smartphone playing a music video"></div>
  <svg class="hero-arrow prev" width="22" height="36" viewBox="0 0 22 36"><path d="M19 3 4 18l15 15" fill="none" stroke="#fff" stroke-width="4"/></svg>
  <svg class="hero-arrow next" width="22" height="36" viewBox="0 0 22 36"><path d="M3 3l15 15L3 33" fill="none" stroke="#fff" stroke-width="4"/></svg>
  <div class="hero-copy">
    <h1>High Quality Mobile Engagement</h1>
    <p>We engage mobile audiences with the right video<br>content at the perfect moment.</p>
    <a href="#" class="btn-orange">Sample App</a>
  </div>
</section>

<section class="partners" aria-label="Partners">
  <span class="partner"></span><span class="partner round"></span><span class="partner"></span><span class="partner round"></span><span class="partner"></span><span class="partner"></span><span class="partner round"></span>
</section>

<section class="why">
  <div class="why-copy">
    <h2 class="section-title">Why Choose Us</h2>
    <ul class="ticks">
      <li>Increase ARPU with new revenue streams.</li>
      <li>Velmora Media is a content platform for operators, that allows them to create new business models based on mobile video.</li>
      <li>Velmora's platforms predictively pre-positions video content, and uses ML to reveal video at the perfect moment for maximum engagement.</li>
    </ul>
    <a href="#" class="btn-grey">Read More</a>
  </div>
  <div class="why-photo" role="img" aria-label="Woman relaxing in a hammock with a tablet"></div>
</section>

<section class="benefits">
  <div class="benefit">
    <svg width="74" height="74" viewBox="0 0 74 74"><circle cx="37" cy="37" r="35" fill="none" stroke="#fff" stroke-width="2"/><rect x="24" y="27" width="26" height="20" fill="none" stroke="#fff" stroke-width="2"/><path d="M26 44l7-8 5 5 4-4 6 7" fill="none" stroke="#fff" stroke-width="2"/><circle cx="43" cy="32" r="2" fill="#fff"/></svg>
    Reach your mobile audience with beautiful HD thumbnails and in-notification videos.
  </div>
  <div class="benefit">
    <svg width="74" height="74" viewBox="0 0 74 74"><circle cx="37" cy="37" r="35" fill="none" stroke="#fff" stroke-width="2"/><path d="M23 27h10l3 3h15v18H23z" fill="none" stroke="#fff" stroke-width="2"/><path d="M34 35v9l7-4.5z" fill="#fff"/></svg>
    Instant video playback, zero buffering, guaranteed flawless playback - even when offline.
  </div>
  <div class="benefit">
    <svg width="74" height="74" viewBox="0 0 74 74"><circle cx="37" cy="37" r="35" fill="none" stroke="#fff" stroke-width="2"/><rect x="27" y="20" width="20" height="34" rx="3" fill="none" stroke="#fff" stroke-width="2"/><circle cx="37" cy="37" r="6" fill="none" stroke="#fff" stroke-width="2"/><path d="M35 34v6l5-3z" fill="#fff"/><path d="M34 50h6" stroke="#fff" stroke-width="2"/></svg>
    Content is personalised based on viewer interests and mobile viewing habits.
  </div>
</section>

<section class="features">
  <div class="features-photo" role="img" aria-label="Woman on a sofa using a tablet"></div>
  <div class="features-copy">
    <h2 class="section-title">Our Features</h2>
    <ul class="ticks">
      <li>The type of content we see as most effective is native vertical video. Think of Flickit 3V ads, but published directly to the phone, rather than a specific app</li>
      <li>Videos are revealed at the right moment based on behavioral models that are built on the device. They appear as notifications, fullscreen videos, overlays or wallpapers. Works for both Kestrel OS and Drover OS.</li>
      <li>The initial target customers are low-cost MVNOs, like Nimbo Mobile and Pellar here in the US, and low-ARPU carriers in APAC, like Orbis in the Philippines</li>
    </ul>
    <a href="#" class="btn-outline">View More</a>
  </div>
</section>

<section class="push">
  <div class="push-copy">
    <h2 class="section-title">Native Push Video</h2>
    <ul class="ticks">
      <li>They'll see around 3 x 15 second video ads per day, at various times based on their usage behavior. The timing is personalized for each individual subscriber. Dana is picking up her phone 150 times per day, and the majority of those times are goal-oriented e.g. checking mail, calendar, calls.</li>
      <li>Other signals include headphones in, in-motion from the accelerometer, whether user has coverage or not</li>
      <li>Also have conversation with a couple of parts of the Costaluz group, including Luma Video in Mexico.</li>
    </ul>
    <a href="#" class="btn-orange">Read More</a>
  </div>
  <div class="push-phones" role="img" aria-label="Two smartphones showing a video wallpaper and a list of movie trailers"></div>
</section>

<section class="orbis">
  <div class="orbis-photo" role="img" aria-label="Faded photo of a café interior"></div>
  <div class="orbis-copy">
    <h2>Orbis also has a young and video-centric subscriber base,<br>which is extremely price sensitive.</h2>
    <p>They have a number of different properties that we can work with.</p>
    <div class="store-badges"><span class="store-badge"></span><span class="store-badge"></span></div>
  </div>
</section>

<footer class="site-footer">
  <div class="foot-col col-links"><h3>Quick Links</h3><a href="#">About Us</a><a href="#">What We Do</a><a href="#">Why We Are</a><a href="#">Blogs</a></div>
  <div class="foot-col col-services"><h3>Our Services</h3><a href="#">Class aptent</a><a href="#">Taciti sociosqu</a><a href="#">Litora torquent</a></div>
  <div class="foot-col col-resources"><h3>Resources</h3><a href="#">FAQ</a><a href="#">Products</a><a href="#">Login</a></div>
  <div class="foot-col col-contact"><h3>Contact Us</h3>
    <span class="field">Name</span><span class="field">Email address</span><span class="field">Phone</span>
    <span class="btn-submit">Submit</span>
  </div>
  <div class="foot-col col-follow"><h3>Follow Us</h3>
    <div class="socials"><span class="social"></span><span class="social"></span><span class="social"></span><span class="social"></span></div>
  </div>
  <div class="foot-rule"></div>
  <p class="copyright">© 2016 Company Name &nbsp;All right reserved &nbsp;Term of Use</p>
  <div class="brand"><span class="brand-mark"></span><span class="brand-name">velmora</span></div>
</footer>

</body>
</html>
```